Gullwing Outfitters - An Alaskan Fishing Charter needs brochure/logo

We need a design for a brochure to advertise our Charter Fishing business. We have two boats and take tourists to fish for Halibut, King Salmon, and other fish. We also do several sight seeing trips for whales, sea lions, waterfalls, eagles, etc...
Website is HookthePelton.example - Promo is a free trip to those who catch largest fish of the season.
We need a whole brand including a picture of the Kraken (whatever that may be) and pictures of local scenery that we can provide.
Updates

Target Market(s)

Tourists visiting Haines, Alaska or looking for Charter Fishing in Alaska

Industry/Entity Type

Business

Logo Text

GULLWING OUTFITTERS

Requirements
Must have
• A logo with picture of Kraken. (our Kraken does not have to be the typical octopus looking Kraken, but we are using the term "Kraken" to mean the largest fish of the year.
Nice to have
• Full Color attractive brochure with catchy logo (supposed to be part of project).
• Pictures of local scenery and catches (we will provide).
• Texts. We included a self drawn sketch of the Kraken and a Halibut as well as other pictures which are copyright protected and are intended only as ideas.

```html
<!DOCTYPE html>
<html lang="en">
<head>
<meta charset="utf-8">
<title>Gullwing Outfitters – Tri-fold Brochure</title>
<link href="https://fonts.googleapis.com/css2?family=Fjalla+One&family=Open+Sans:wght@400;600&display=swap" rel="stylesheet">
<style>
  :root{
    --page:#bdbdbd;
    --ink-dark:#231d1a;
    --orange:#f6a400;
    --yellow:#ffd200;
    --blue:#0d4a9c;
    --sky:#2a8fd8;
    --white:#ffffff;
    --body-grey:#d9d6d3;
  }
  *{margin:0;padding:0;box-sizing:border-box}
  html,body{width:938px;height:1200px;overflow:hidden;background:var(--page)}
  .brochure{position:absolute;left:29px;top:258px;width:880px;height:684px;overflow:hidden;box-shadow:0 6px 18px rgba(0,0,0,.35)}
  .brochure-art{position:absolute;inset:0}
  .copy{position:absolute;font-family:'Open Sans',sans-serif;color:var(--white)}
  .heading{font-family:'Fjalla One',sans-serif;text-transform:uppercase;line-height:1}

  .captain{left:28px;top:330px}
  .captain .role{font-size:27px;color:var(--white)}
  .captain .name{font-size:31px;color:var(--orange);margin-top:2px}
  .services{left:28px;top:410px;width:250px;font-size:10.5px;line-height:1.4;color:var(--body-grey)}
  .services p+p{margin-top:10px}
  .services .accent{color:var(--sky);font-weight:600;font-size:14px}

  .trips{left:297px;width:289px;top:44px;text-align:center}
  .trips .label{font-size:19px;color:var(--ink-dark)}
  .trips .hours{font-size:28px;color:var(--blue);margin:4px 0 10px}

  .contact{left:297px;width:289px;top:505px;text-align:center;font-size:13px;line-height:1.45}
  .contact .label{font-size:20px;color:var(--white)}
  .contact .phone{font-size:26px;color:var(--orange);margin:6px 0 8px}
  .contact .social{margin-top:8px}

  .brand-name{left:620px;top:82px;width:240px;text-align:center;font-family:'Fjalla One',sans-serif;color:var(--orange);font-size:30px;line-height:1.2;text-transform:uppercase}

  .cover-title{left:586px;width:294px;top:556px;text-align:center}
  .cover-title .name{font-family:'Fjalla One',sans-serif;font-size:34px;line-height:1.1;color:var(--white);text-transform:uppercase}
  .cover-title .web{font-size:13px;color:var(--white);margin-top:10px}
</style>
</head>
<body>
<main class="brochure">
  <svg class="brochure-art" viewBox="0 0 880 684" width="880" height="684">
    <defs>
      <linearGradient id="midPanel" x1="0" y1="0" x2="0" y2="1">
        <stop offset="0" stop-color="#f5f5f5"/><stop offset="1" stop-color="#d4d4d4"/>
      </linearGradient>
      <linearGradient id="catchPhoto" x1="0" y1="0" x2="0" y2="1">
        <stop offset="0" stop-color="#8fb6d6"/><stop offset=".45" stop-color="#4f7f9c"/><stop offset="1" stop-color="#3a3f46"/>
      </linearGradient>
      <linearGradient id="shorePhoto" x1="0" y1="0" x2="0" y2="1">
        <stop offset="0" stop-color="#5aa7e6"/><stop offset=".35" stop-color="#c9d7e2"/><stop offset=".6" stop-color="#4c5a3a"/><stop offset="1" stop-color="#2b3a3d"/>
      </linearGradient>
      <linearGradient id="mapArea" x1="0" y1="0" x2="1" y2="1">
        <stop offset="0" stop-color="#e9eef2"/><stop offset=".5" stop-color="#7f97a3"/><stop offset="1" stop-color="#d6dde2"/>
      </linearGradient>
      <linearGradient id="warmBand" x1="0" y1="0" x2="1" y2="0">
        <stop offset="0" stop-color="var(--orange)"/><stop offset="1" stop-color="var(--yellow)"/>
      </linearGradient>
    </defs>

    <rect class="base" width="880" height="684" fill="var(--ink-dark)"/>

    <path class="mid-field" d="M297 0H586V250C520 300 470 300 420 270C380 250 340 300 297 330Z" fill="url(#midPanel)"/>

    <rect class="cover-top" x="586" y="0" width="294" height="240" fill="var(--white)"/>

    <path role="img" aria-label="Photo: captain and young angler holding two large halibut on deck, mountains behind" d="M0 0H297V318C210 258 100 244 0 266Z" fill="url(#catchPhoto)"/>

    <path class="warm-swoosh" d="M0 262C110 240 230 262 330 340L345 380C240 300 120 278 0 300Z" fill="url(#warmBand)"/>
    <path class="warm-swoosh" d="M470 300C520 260 560 230 640 200L880 150V172L650 228C580 250 530 290 490 330Z" fill="url(#warmBand)"/>

    <path role="img" aria-label="Photo: white lighthouse on a rocky island with snowy mountains" d="M586 250C640 225 760 190 880 172V560C760 520 650 500 586 490Z" fill="url(#shorePhoto)"/>

    <path class="blue-swoosh" d="M380 440C470 470 560 430 640 470C720 505 800 520 880 510V540C790 560 700 530 620 500C540 470 470 500 380 460Z" fill="var(--blue)"/>
    <path class="yellow-line" d="M560 470C650 480 740 530 880 525V532C740 545 650 495 560 480Z" fill="var(--yellow)"/>

    <circle cx="438" cy="362" r="108" fill="url(#warmBand)"/>
    <circle role="img" aria-label="Satellite map of the fjords around Haines and Skagway" cx="438" cy="362" r="98" fill="url(#mapArea)"/>

    <circle cx="740" cy="110" r="150" fill="url(#warmBand)"/>
    <circle cx="740" cy="108" r="138" fill="var(--white)"/>

    <path role="img" aria-label="Silhouette of a wolf on a rocky ridge" d="M0 610C60 560 140 580 190 600C230 610 270 590 297 600V684H0Z" fill="#2c2522"/>
  </svg>

  <div class="copy captain">
    <div class="heading role">Captain</div>
    <div class="heading name">Dale Morrow</div>
  </div>

  <div class="copy services">
    <p>Charter fishing for King Salmon, Halibut, Cod, and many other sea dwellers.</p>
    <p><span class="accent">Sight Seeing trips</span> for humpback whales, Orcas, Eagles, waterfalls, seals, SeaLions, and other local wildlife such as Grizzly Bear, Black Bear, Moose, Wolf,</p>
  </div>

  <div class="copy trips">
    <div class="heading label">Half Day Trips</div>
    <div class="heading hours">4 Hours</div>
    <div class="heading label">Full Day Trips</div>
    <div class="heading hours">8 Hours</div>
  </div>

  <div class="copy contact">
    <div class="heading label">Call us at</div>
    <div class="heading phone">+1 555-014-2290</div>
    <div>88 Wharf Street</div>
    <div>Port Lantern, Alaska</div>
    <div class="social">@gullwingsportfishing</div>
    <div>www.HookthePelton.example</div>
  </div>

  <div class="copy brand-name">Gullwing<br>Outfitters</div>

  <div class="copy cover-title">
    <div class="name">Gullwing Outfitters</div>
    <div class="web">www.HookthePelton.example</div>
  </div>
</main>
</body>
</html>
```